Lumora Systems New Website - IT Infrastructure | Smart Cabinet | Micro Data Center

We're an IT SI providing Server Room Design & Build | All-in-One Rack & Smart Cabinet | Structured Cabling | IT Relocation | Maintenance. Old website can be found at www.lumorasys.com.hk. We'd like a brand new wix website which is modern, minimalist, interactive with some animation. Website content will be mostly static and include our service, our project, news and events, about us, contacts, blogs, partners and brands, etc.

reference sites:
We'd like to see more designs referring to below

https://www.pixelvane.example/design/41736205
https://www.pixelvane.example/design/41892417
https://velbrinn.example/

Animation (scrolling effect) referring to
https://velbrinn.example/intelligence/smart-office-room/
Updates

we'd like below style.

Designs look the same

Target Market(s)

Commercials in HK

Industry/Entity Type

IT, Technology, Data Center

Coding

Coded - Design and coding required

Font styles to use
Sans Serif

Requirements
Must have
• CMS, Some Interactive Elements/ Graphics

```html
<!DOCTYPE html>
<html lang="en">
<head>
<meta charset="utf-8">
<title>Lumora Systems — Smart &amp; Flawless Data Connectivity</title>
<link rel="stylesheet" href="https://fonts.googleapis.com/css2?family=Poppins:wght@300;400;500;600;700&display=swap">
<style>
:root{
  --navy:#1b2250;
  --navy-deep:#141a3c;
  --hero:#1f2a5a;
  --orange:#f2841a;
  --orange-soft:#f59a3c;
  --ink:#1c1f2e;
  --muted:#6f7385;
  --grey-bg:#f3f3f5;
  --dark:#262626;
  --white:#ffffff;
  --line:#e4e5ea;
}
*{box-sizing:border-box;margin:0;padding:0}
html,body{width:1200px;height:5107px;overflow:hidden}
body{position:relative;font-family:"Poppins",sans-serif;color:var(--ink);background:var(--white)}
.abs{position:absolute}
.ph{position:absolute}
.eyebrow{color:var(--orange);font-size:15px;font-weight:500}
.h2{font-size:32px;font-weight:600;color:var(--ink);line-height:1.25}
.center{text-align:center;left:0;right:0}
.btn{position:absolute;background:var(--orange);color:#fff;font-size:10px;font-weight:600;display:flex;align-items:center;justify-content:center;gap:14px;border-radius:3px;letter-spacing:.3px}
.body-text{font-size:12.5px;line-height:22px;color:var(--muted)}

/* hero */
.hero{position:absolute;left:0;top:0;width:1200px;height:674px;overflow:hidden}
.hero-bg{position:absolute;inset:0;background:linear-gradient(120deg,#101735 0%,#1d2f6b 45%,#2a3d7e 70%,#1c2654 100%)}
.hero-cut{position:absolute;left:0;top:0}
.nav{position:absolute;left:357px;top:0;width:456px;height:50px;background:#fff;border-radius:0 0 40px 40px;display:flex;justify-content:center;align-items:center;gap:38px;font-size:10px;font-weight:500;color:var(--ink)}
.nav .on{color:var(--navy);font-weight:600}
.logo{position:absolute;display:flex;align-items:center;gap:8px;color:var(--orange);font-weight:600}
.logo .mark{width:22px;height:22px;border:3px solid var(--orange);border-radius:4px}
.hero-phone{position:absolute;left:905px;top:16px;display:flex;gap:10px;align-items:center;color:#fff}
.hero-phone small{display:block;font-size:7px;opacity:.85}
.hero-phone b{font-size:9px;font-weight:600}
.socials{position:absolute;left:48px;top:270px;display:flex;flex-direction:column;gap:17px}
.socials span{width:24px;height:24px;border:1px solid rgba(255,255,255,.7);border-radius:50%}
.socials span.on{background:#27a2e0;border-color:#27a2e0}
.hero h1{position:absolute;left:228px;top:210px;color:#fff;font-size:43px;font-weight:600;line-height:60px}
.hero p{position:absolute;left:234px;top:342px;color:#fff;font-size:12.5px;line-height:22px}

/* services */
.svc-card{position:absolute;width:320px;height:443px}
.svc-info{position:absolute;background:var(--navy);color:#fff;text-align:center;padding:24px 20px}
.svc-info h3{font-size:23px;font-weight:500;line-height:33px}
.svc-info p{font-size:11.5px;line-height:21px;margin-top:12px;opacity:.9}
.svc-info .go{width:34px;height:34px;border:2px solid #fff;border-radius:50%;margin:16px auto 0;display:flex;align-items:center;justify-content:center}

/* why */
.feature{position:absolute;left:650px;display:flex;gap:24px}
.feature .ic{width:66px;height:66px;border:2px solid rgba(255,255,255,.8);border-radius:50%;flex:none}
.feature h4{color:#fff;font-size:16px;font-weight:600}
.feature p{color:#fff;font-size:12px;line-height:22px;opacity:.95;margin-top:4px}

/* team */
.member{position:absolute;top:2909px;width:234px;height:327px;background:#fff;box-shadow:0 6px 22px rgba(20,26,60,.1)}
.member .ph{left:0;top:0;width:234px;height:235px}
.member .plus{position:absolute;right:22px;top:220px;width:28px;height:28px;background:#fff;box-shadow:0 2px 8px rgba(0,0,0,.15);display:flex;align-items:center;justify-content:center;font-size:16px;color:var(--ink)}
.member .role{position:absolute;left:26px;top:264px;font-size:10px;color:var(--orange)}
.member .name{position:absolute;left:26px;top:284px;font-size:15px;font-weight:600}
.member.dark{background:#3a3a3c}
.member.dark .name{color:#fff}
.member.dark .role{color:#999}
.member .soc{position:absolute;right:12px;top:40px;display:flex;flex-direction:column;gap:12px}
.member .soc span{width:30px;height:30px;background:#fff;display:block}

/* quote form */
.field{position:absolute;border:1px solid #777;border-radius:3px;color:#aaa;font-size:9px;padding:8px 14px}

/* footer */
.footer{position:absolute;left:0;top:4527px;width:1200px;height:580px;background:var(--navy-deep)}
.ft-h{position:absolute;color:#fff;font-size:20px;font-weight:600}
.ft-h::after{content:"";position:absolute;left:0;top:42px;width:42px;height:4px;background:var(--orange)}
.links{position:absolute;font-size:13px;color:#fff;line-height:31px;list-style:none}
.links li::before{content:"›";margin-right:12px}
.info-bar{position:absolute;left:85px;top:431px;width:1026px;height:85px;background:#23295a;display:flex}
.info-bar div{flex:1;display:flex;align-items:center;gap:22px;padding-left:28px;color:#fff;font-size:14px;border-right:1px solid rgba(255,255,255,.2)}
.info-bar div:last-child{border-right:none}
.info-bar b{display:block;font-weight:600;font-size:14px}
</style>
</head>
<body>

<!-- HERO -->
<section class="hero">
  <div class="hero-bg" role="img" aria-label="Photo of two colleagues reviewing a tablet in a blue-lit server room"></div>
  <svg class="hero-cut" width="1200" height="674" viewBox="0 0 1200 674">
    <path d="M0 674 L0 600 Q0 560 60 600 Q150 660 380 665 Q400 610 460 608 L1200 608 L1200 674 Z" fill="#fff"/>
  </svg>
  <div class="logo" style="left:136px;top:24px;font-size:21px"><span class="mark"></span>Lumora</div>
  <nav class="nav"><span class="on">HOME</span><span>ABOUT</span><span>SERVICES</span><span>CASES</span><span>BLOG</span><span>CONTACT</span></nav>
  <div class="hero-phone">
    <svg width="20" height="20" viewBox="0 0 24 24" fill="none" stroke="#fff" stroke-width="2"><path d="M22 16.9v3a2 2 0 0 1-2.2 2A19.8 19.8 0 0 1 2.1 4.2 2 2 0 0 1 4.1 2h3a2 2 0 0 1 2 1.7l.5 3a2 2 0 0 1-.6 1.8L7.7 9.8a16 16 0 0 0 6.5 6.5l1.3-1.3a2 2 0 0 1 1.8-.6l3 .5a2 2 0 0 1 1.7 2z"/></svg>
    <div><small>Have Any Questions?</small><b>+852 3915 7240</b></div>
  </div>
  <div class="socials"><span></span><span></span><span class="on"></span><span></span></div>
  <h1>Smart &amp; Flawless<br>Data Connectivity</h1>
  <p>Lorem ipsum dolor sit amet, consectetur adipiscing elit, sed<br>do eiusmod tempor incididunt ut labore et dolore magna aliqua.</p>
  <div class="btn" style="left:234px;top:404px;width:152px;height:42px">READ MORE <span>→</span></div>
</section>

<!-- ABOUT -->
<section>
  <div class="eyebrow abs" style="left:117px;top:820px">About Us</div>
  <div class="h2 abs" style="left:117px;top:845px">Your Data, Our Priority</div>
  <p class="body-text abs" style="left:123px;top:914px;font-size:12px">Lorem ipsum dolor sit amet, consectetur adipiscing elit, sed<br>do eiusmod tempor incididunt ut labore et dolore magna aliqua.<br>Ut enim ad minim veniam, q</p>
  <p class="abs" style="left:123px;top:998px;color:var(--orange);font-size:16px;line-height:26px">"Driving Success through Data<br>Infrastructure"</p>
  <div class="ph" style="left:573px;top:791px;width:524px;height:402px;background:linear-gradient(135deg,#1a2a6e,#3b5bd8 50%,#16205a)" role="img" aria-label="Photo of a data centre aisle with server racks"></div>
  <div class="abs" style="left:1120px;top:794px;width:4px;height:218px;background:#3fa9e0"></div>
  <div class="abs" style="left:818px;top:1209px;width:278px;height:4px;background:#3fa9e0"></div>
  <div class="ph" style="left:121px;top:1101px;width:325px;height:221px;background:linear-gradient(135deg,#4b5563,#9aa3ad 55%,#3a414a)" role="img" aria-label="Photo of a technician working on network cabling"></div>
  <div class="ph" style="left:476px;top:1101px;width:325px;height:221px;background:linear-gradient(135deg,#8fc9c6,#4f9a9a 60%,#2a3240)" role="img" aria-label="Photo of two business professionals standing together"></div>
  <div class="abs" style="left:801px;top:1097px;width:12px;height:229px;background:#fff"></div>
</section>

<!-- SERVICES -->
<section class="abs" style="left:0;top:1408px;width:1200px;height:704px;background:var(--grey-bg)">
  <div class="eyebrow abs center" style="top:64px">Our Latest Services</div>
  <div class="h2 abs center" style="top:92px">Services We Provide</div>

  <div class="svc-card" style="left:93px;top:190px">
    <div class="ph" style="left:0;top:0;width:320px;height:400px;background:linear-gradient(160deg,#e6e2dc,#b7b0a7 60%,#3d3a36)" role="img" aria-label="Photo of a smiling professional in a dark sweater"></div>
    <div class="svc-info" style="left:28px;top:215px;width:264px;height:228px">
      <h3>Data Centre<br>Building</h3><p>Lorem ipsum dolor sit amet, ae<br>consectetur adipiscing</p>
      <div class="go"><svg width="14" height="14" viewBox="0 0 14 14"><path d="M5 3l4 4-4 4" stroke="#fff" stroke-width="2" fill="none"/></svg></div>
    </div>
  </div>
  <div class="svc-card" style="left:438px;top:190px">
    <div class="ph" style="left:0;top:42px;width:322px;height:401px;background:linear-gradient(160deg,#3c4a6e,#1c2340 60%,#0d1226)" role="img" aria-label="Photo of an engineer between server racks"></div>
    <div class="svc-info" style="left:28px;top:0;width:264px;height:223px">
      <h3>Structured<br>Cabling</h3><p>Lorem ipsum dolor sit amet, ae<br>consectetur adipiscing</p>
      <div class="go"><svg width="14" height="14" viewBox="0 0 14 14"><path d="M5 3l4 4-4 4" stroke="#fff" stroke-width="2" fill="none"/></svg></div>
    </div>
  </div>
  <div class="svc-card" style="left:787px;top:190px">
    <div class="ph" style="left:0;top:0;width:320px;height:400px;background:linear-gradient(160deg,#5b6578,#c8d0dc 55%,#9aa5b8)" role="img" aria-label="Photo of a bright server corridor"></div>
    <div class="svc-info" style="left:28px;top:215px;width:264px;height:228px">
      <h3>Audio-Visual<br>for Conferences</h3><p>Lorem ipsum dolor sit amet, ae<br>consectetur adipiscing</p>
      <div class="go"><svg width="14" height="14" viewBox="0 0 14 14"><path d="M5 3l4 4-4 4" stroke="#fff" stroke-width="2" fill="none"/></svg></div>
    </div>
  </div>
</section>

<!-- WHY US -->
<section>
  <div class="abs" style="left:0;top:2181px;width:620px;height:496px;background:var(--navy)"></div>
  <div class="ph" style="left:601px;top:2148px;width:599px;height:559px;background:linear-gradient(135deg,#f5962e,#e0700f 60%,#c85f0a)" role="img" aria-label="Orange-toned photo of a server room"></div>
  <div class="abs" style="left:559px;top:2237px;width:472px;height:391px;border:3px solid #fff"></div>
  <div class="abs" style="left:1033px;top:2237px;width:42px;height:100px;background:#fff;display:flex;align-items:center;justify-content:center"><span style="transform:rotate(-90deg);white-space:nowrap;font-size:11px;font-weight:600">GET A QUOTE</span></div>
  <div class="abs" style="left:117px;top:2281px;color:var(--orange);font-size:15px;font-weight:500">Why we are the Best</div>
  <div class="abs" style="left:117px;top:2305px;color:#fff;font-size:32px;font-weight:600;line-height:46px">Where Ideas Meet<br>Implementation</div>
  <p class="abs" style="left:123px;top:2416px;color:#fff;font-size:12px;line-height:22px">Lorem ipsum dolor sit amet, consectetur adipiscing elit, sed<br>do eiusmod tempor incididunt ut labore et dolore magna aliqua.<br>Ut enim ad minim veniam, q</p>
  <div class="btn" style="left:127px;top:2532px;width:152px;height:43px">READ MORE <span>→</span></div>

  <div class="feature" style="top:2272px"><span class="ic"></span><div><h4>Customized Solutions</h4><p>Lorem ipsum dolor sit amet, consecte<br>tur adipiscing elit, sed do</p></div></div>
  <div class="feature" style="top:2384px"><span class="ic"></span><div><h4>Client-Centric</h4><p>Lorem ipsum dolor sit amet, consecte<br>tur adipiscing elit, sed do</p></div></div>
  <div class="feature" style="top:2496px"><span class="ic"></span><div><h4>Professionalism</h4><p>Lorem ipsum dolor sit amet, consecte<br>tur adipiscing elit, sed do</p></div></div>
</section>

<!-- TEAM -->
<section>
  <div class="eyebrow abs center" style="top:2785px">Our Team</div>
  <div class="h2 abs center" style="top:2812px">Our Experienced Team</div>

  <div class="member" style="left:93px">
    <div class="ph" style="background:linear-gradient(160deg,#c9d3dc,#8a98a6 60%,#2e3440)" role="img" aria-label="Portrait of a team founder"></div>
    <div class="plus">+</div><div class="role">Founder</div><div class="name">Elan V. Marsh</div>
  </div>
  <div class="member dark" style="left:353px">
    <div class="ph" style="background:linear-gradient(160deg,#6f7480,#474b55 60%,#2c2f36)" role="img" aria-label="Portrait of the CTO holding a tablet"></div>
    <div class="soc"><span style="background:#27a2e0"></span><span></span><span></span><span></span><span style="background:var(--orange)"></span></div>
    <div class="role">CTO</div><div class="name">Elan V. Marsh</div>
  </div>
  <div class="member" style="left:615px">
    <div class="ph" style="background:linear-gradient(160deg,#d8dde3,#9aa6b6 60%,#4b5a70)" role="img" aria-label="Portrait of a team founder"></div>
    <div class="plus">+</div><div class="role">Founder</div><div class="name">Elan V. Marsh</div>
  </div>
  <div class="member" style="left:875px">
    <div class="ph" style="background:linear-gradient(160deg,#8a6a52,#b79a80 55%,#5e7aa0)" role="img" aria-label="Portrait of a team founder"></div>
    <div class="plus">+</div><div class="role">Founder</div><div class="name">Elan V. Marsh</div>
  </div>
</section>

<!-- QUOTE -->
<section class="abs" style="left:0;top:3341px;width:1200px;height:581px;background:var(--dark)">
  <div class="abs" style="left:0;top:0;width:454px;height:581px;background:linear-gradient(180deg,#f28a1e,#d9700e)"></div>
  <div class="abs" style="left:0;top:99px;width:585px;height:3px;background:rgba(255,255,255,.35)"></div>
  <div class="abs" style="left:0;top:478px;width:585px;height:3px;background:rgba(255,255,255,.35)"></div>
  <div class="ph" style="left:139px;top:40px;width:446px;height:541px;background:linear-gradient(160deg,#3a3d4a,#22242c 70%)" role="img" aria-label="Photo of two business professionals standing back to back"></div>
  <div class="abs" style="left:44px;top:468px;transform:rotate(-90deg);transform-origin:left top;color:#fff;font-size:34px;font-weight:700;white-space:nowrap">GET A FREE QUOTE</div>
  <div class="abs" style="left:630px;top:85px;color:var(--orange);font-size:15px;font-weight:500">Contact Us</div>
  <div class="abs" style="left:630px;top:108px;color:#fff;font-size:32px;font-weight:600">GET A FREE QUOTE</div>
  <div class="field" style="left:633px;top:183px;width:206px;height:34px">Your Name</div>
  <div class="field" style="left:865px;top:183px;width:206px;height:34px">Phone Number</div>
  <div class="field" style="left:633px;top:241px;width:206px;height:34px">Email Address</div>
  <div class="field" style="left:865px;top:241px;width:206px;height:34px">Location</div>
  <div class="field" style="left:633px;top:300px;width:438px;height:135px">Your Message</div>
  <div class="btn" style="left:627px;top:467px;width:150px;height:42px">READ MORE <span>→</span></div>
</section>

<!-- TESTIMONIALS -->
<section>
  <div class="eyebrow abs center" style="top:4022px">Our Testimonials</div>
  <div class="h2 abs center" style="top:4050px">Client Reviews</div>
  <div class="ph" style="left:99px;top:4135px;width:137px;height:287px;background:linear-gradient(160deg,#3a4a78,#1c2448)" role="img" aria-label="Photo of a previous client"></div>
  <svg class="abs" style="left:148px;top:4266px" width="38" height="24" viewBox="0 0 38 24"><path d="M36 12H4M14 2L3 12l11 10" stroke="#fff" stroke-width="3" fill="none"/></svg>
  <div class="abs" style="left:262px;top:4135px;width:676px;height:287px;background:#fff;box-shadow:0 6px 26px rgba(20,26,60,.1)"></div>
  <div class="ph" style="left:262px;top:4135px;width:225px;height:287px;background:linear-gradient(160deg,#c7ccd4,#7d8593 60%,#3e4450)" role="img" aria-label="Portrait of a smiling client"></div>
  <div class="abs" style="left:530px;top:4178px;color:var(--navy);font-size:38px;font-weight:700;line-height:30px">“</div>
  <p class="abs" style="left:530px;top:4226px;font-size:12px;line-height:22px;color:var(--muted)">Lorem ipsum dolor sit amet, consectetur adipiscing elit,<br>sed do eiusmod tempor incididunt ut labore et dolore<br>magna aliqua. Ut enim ad minim veniam, qdidunt ut<br>labore et dolore magna aliqua.</p>
  <div class="abs" style="left:532px;top:4335px;font-size:17px;font-weight:500">Corin Halbrook</div>
  <div class="abs" style="left:532px;top:4360px;font-size:10px;color:var(--muted)">Chairperson</div>
  <div class="abs" style="left:824px;top:4337px;color:var(--orange);font-size:14px;letter-spacing:2px">★★★★★</div>
  <div class="ph" style="left:962px;top:4135px;width:137px;height:287px;background:linear-gradient(160deg,#2e3a66,#4a5c96)" role="img" aria-label="Photo of a previous client"></div>
  <svg class="abs" style="left:1017px;top:4266px" width="38" height="24" viewBox="0 0 38 24"><path d="M2 12h32M24 2l11 10-11 10" stroke="#fff" stroke-width="3" fill="none"/></svg>
</section>

<!-- FOOTER -->
<footer class="footer">
  <div class="logo" style="left:74px;top:90px;font-size:32px"><span class="mark" style="width:32px;height:32px"></span>Lumora</div>
  <div class="abs" style="left:83px;top:170px;color:#fff;font-size:17px;font-weight:600">852-390-1180</div>
  <div class="abs" style="left:83px;top:196px;color:#fff;font-size:12px;font-weight:600">Call for free consultation</div>
  <p class="abs" style="left:83px;top:224px;color:#fff;font-size:12px;line-height:22px">Lorem ipsum dolor sit amet, consectet<br>sed do eiusmod tempor incididunt ut la<br>magna aliqua. Ut enim</p>
  <div class="abs" style="left:83px;top:298px;color:#fff;font-size:13px;font-weight:600">Read more ›</div>

  <div class="ft-h" style="left:437px;top:95px">Useful Links</div>
  <ul class="links" style="left:441px;top:167px"><li>About Company</li><li>Leadership</li><li>Blog Post</li><li>FAQ'S</li><li>Certification</li><li>Testimonials</li></ul>
  <ul class="links" style="left:606px;top:167px"><li>Services</li><li>Industries</li><li>Feedback</li><li>Partners</li><li>Pricing</li><li>Contct</li></ul>

  <div class="ft-h" style="left:790px;top:95px">Newsletter</div>
  <p class="abs" style="left:787px;top:190px;color:#fff;font-size:11.5px;line-height:25px;font-weight:500">Dont miss to subscribe to our news feeds, kindly<br>fill the form below</p>
  <div class="abs" style="left:787px;top:260px;width:320px;height:50px;background:#23295a;border-radius:25px;color:#fff;font-size:11px;font-weight:500;padding:16px 26px">Your Email Address</div>
  <div class="abs" style="left:1057px;top:260px;width:50px;height:50px;background:var(--orange);border-radius:0 25px 25px 0;display:flex;align-items:center;justify-content:center"><svg width="14" height="14" viewBox="0 0 14 14"><path d="M5 2l5 5-5 5" stroke="#fff" stroke-width="2" fill="none"/></svg></div>

  <div class="info-bar">
    <div><svg width="28" height="30" viewBox="0 0 24 26" fill="none" stroke="#f2841a" stroke-width="2"><path d="M12 24s8-7.5 8-14a8 8 0 0 0-16 0c0 6.5 8 14 8 14z"/><circle cx="12" cy="10" r="3"/></svg><span><b>Location</b>246 Rd, Country</span></div>
    <div><svg width="30" height="28" viewBox="0 0 26 24" fill="none" stroke="#f2841a" stroke-width="2"><rect x="2" y="3" width="22" height="15" rx="2"/><path d="M7 18v4l5-4M7 9h12M7 13h8"/></svg><span><b>Mail us</b>hello@lumorasys.example</span></div>
    <div><svg width="30" height="28" viewBox="0 0 24 24" fill="none" stroke="#f2841a" stroke-width="2"><path d="M22 2L11 13M22 2l-7 20-4-9-9-4z"/></svg><span><b>Office hrs</b>9.00am to 7.00pm (Mon-Sat)</span></div>
  </div>
  <div class="abs" style="left:1125px;top:497px;width:48px;height:48px;background:var(--orange);border-radius:4px;display:flex;align-items:center;justify-content:center"><svg width="16" height="16" viewBox="0 0 16 16"><path d="M3 11l5-5 5 5" stroke="#fff" stroke-width="2.5" fill="none"/></svg></div>
  <div class="abs" style="left:0;top:531px;width:1200px;height:49px;background:#fff"></div>
  <div class="abs" style="left:85px;top:548px;font-size:12px;color:var(--ink)">Lumora Systems</div>
  <div class="abs" style="left:801px;top:548px;font-size:12px;color:var(--muted);display:flex;gap:22px"><span>Privacy Policy</span><span>Terms &amp; Conditions</span><span>Site Map</span></div>
</footer>

</body>
</html>
```